Need A Standard Musical Download Website

We are looking for a talented designer to create a unique web design for our startup Music website called Vorde Sound.
The website should be responsive and filled with some creative stuffs along with bright colors.

Vorde sound is a website loaded with different types of music and capable of downloading the requested music by its users.
There will be categories of music which would be sorted by the genre. They include RnB, Hip-Hop, Afro pop, Pop, Dancehall and Reggae).

DESIGN STYLE/THEME

Creative, trendy, colorful, unique, and easy to use. You have freedom of selecting which ever color suits you. The design must be energetic and attractive.

NAVIGATION

HOME-MUSIC(RnB, Hip hop, Afro pop, POP, dancehall, Reggae)-ARTISTE-NEWS-LOGIN

PAGES REQUIRED
------------
1)Home Page
2)Music

FONTS
GOOGLE FONTS is strongly recommended.

Designers can get inspiration from https://tunabrook.example

Industry/Entity Type

Startup

```html
<!DOCTYPE html>
<html lang="en">
<head>
<meta charset="utf-8">
<title>Vorde Sound</title>
<link href="https://fonts.googleapis.com/css2?family=Lato:wght@300;400;700;900&display=swap" rel="stylesheet">
<style>
:root{
  --red:#d10a0a;
  --ink:#111;
  --text:#333;
  --muted:#888;
  --line:#cfcfcf;
  --footer:#efefef;
  --card-alt:#f0f0f0;
  --dark-btn:#1e1e1e;
}
*{box-sizing:border-box;margin:0;padding:0}
html,body{width:1200px;height:1086px;overflow:hidden;background:#fff}
body{position:relative;font-family:'Lato',sans-serif;color:var(--text)}
.site-header{position:absolute;left:0;top:0;width:1200px;height:91px;border-bottom:1px solid #ddd;background:#fff}
.brand{position:absolute;left:115px;top:26px;font-size:35px;font-weight:400;color:var(--ink);letter-spacing:.5px}
.main-nav{position:absolute;top:37px;font-size:16.5px;letter-spacing:.5px}
.main-nav a{position:absolute;color:#999;text-decoration:none;white-space:nowrap}
.main-nav a.active{color:#222}
.login-btn{position:absolute;left:971px;top:28px;width:106px;height:38px;background:var(--red);color:#fff;font-size:16.5px;display:flex;align-items:center;justify-content:center;letter-spacing:.5px}
.hero{position:absolute;left:0;top:91px;width:1200px;height:581px;overflow:hidden}
.hero-photo{position:absolute;inset:0;background:
  radial-gradient(ellipse at 40% 30%,rgba(220,180,150,.55),transparent 45%),
  radial-gradient(ellipse at 50% 75%,rgba(70,110,160,.55),transparent 40%),
  linear-gradient(90deg,#5a3020 0%,#8a4a2c 30%,#a0603a 55%,#7a4028 80%,#5e3522 100%)}
.hero-shade{position:absolute;inset:0;background:linear-gradient(90deg,rgba(0,0,0,.35),rgba(0,0,0,.1) 60%,rgba(0,0,0,.15))}
.hero h1{position:absolute;left:129px;top:190px;font-size:45px;line-height:51px;font-weight:700;color:#fff;letter-spacing:.5px}
.hero p{position:absolute;left:129px;top:301px;width:500px;font-size:16.5px;line-height:29px;color:#fff}
.btn{position:absolute;display:flex;align-items:center;justify-content:center;color:#fff;font-weight:700;font-size:18.5px}
.btn-download{left:129px;top:375px;width:175px;height:45px;background:var(--red)}
.btn-listen{left:312px;top:375px;width:175px;height:45px;background:var(--dark-btn)}
.dots{position:absolute;left:557px;top:535px;display:flex;gap:10px}
.dots span{width:14px;height:14px;border-radius:50%;background:#fff}
.dots span.on{background:transparent;border:2px solid #fff}
.features{position:absolute;left:118px;top:697px;width:964px;height:204px;border:1px solid var(--line);display:flex}
.feature{position:relative;width:321px;height:100%;overflow:hidden;background:#fff}
.feature+.feature{border-left:1px solid var(--line)}
.feature.alt{background:var(--card-alt)}
.feature-art{position:absolute;top:0;bottom:0}
.feature h2{position:absolute;left:32px;top:32px;font-size:23px;line-height:27px;font-weight:400;color:#222;letter-spacing:.3px;z-index:1}
.feature.alt h2{color:var(--red)}
.feature p{position:absolute;left:32px;top:92px;width:175px;font-size:11.5px;line-height:17px;color:var(--muted);z-index:1}
.feature .more{position:absolute;left:31px;top:140px;width:103px;height:32px;border:1px solid #bbb;background:#f6f6f6;font-size:14px;color:#444;display:flex;align-items:center;justify-content:center;z-index:1}
.feature .more.primary{background:var(--red);border-color:var(--red);color:#fff}
.site-footer{position:absolute;left:0;top:956px;width:1200px;height:130px;background:var(--footer)}
.footer-nav a{position:absolute;top:38px;font-size:15px;color:#333;text-decoration:none;letter-spacing:.3px}
.copyright{position:absolute;left:127px;top:68px;font-size:14px;color:#888;word-spacing:1px}
.social{position:absolute;left:941px;top:36px;display:flex;gap:3px}
.social span{width:32px;height:32px;border:2px solid #555;border-radius:50%}
</style>
</head>
<body>
<header class="site-header">
  <div class="brand">Vorde Sound</div>
  <nav class="main-nav">
    <a class="active" style="left:561px">HOME</a>
    <a style="left:662px">MUSIC</a>
    <a style="left:763px">ARTISTE</a>
    <a style="left:877px">NEWS</a>
  </nav>
  <div class="login-btn">LOGIN</div>
</header>

<section class="hero">
  <div class="hero-photo" role="img" aria-label="Young man wearing headphones and sunglasses sitting on steps with a laptop and phone"></div>
  <div class="hero-shade"></div>
  <h1>Listen Different type of<br>Music and Download</h1>
  <p>Class aptent taciti sociosqu ad litora torquent per conubia nostra per inceptos hymenaeos Proin nulla</p>
  <div class="btn btn-download">Download</div>
  <div class="btn btn-listen">Listen Song</div>
  <div class="dots"><span class="on"></span><span></span><span></span><span></span></div>
</section>

<section class="features">
  <article class="feature">
    <div class="feature-art" role="img" aria-label="Colourful music notes with butterflies" style="left:200px;width:115px;background:radial-gradient(ellipse at 50% 50%,rgba(230,60,60,.35),rgba(255,200,60,.15) 45%,transparent 70%)"></div>
    <h2>Discover Your<br>Songs Collection</h2>
    <p>Class aptent taciti sociosqu ad litora torquent per con</p>
    <div class="more">Read More</div>
  </article>
  <article class="feature alt">
    <div class="feature-art" role="img" aria-label="Smartphone with earphones showing a music app" style="left:200px;width:121px;background:radial-gradient(ellipse at 55% 55%,rgba(40,40,40,.45),rgba(200,200,200,.2) 45%,transparent 70%)"></div>
    <h2>Unlimited Songs<br>Download</h2>
    <p>Class aptent taciti sociosqu ad litora torquent per co</p>
    <div class="more primary">Click here</div>
  </article>
  <article class="feature">
    <div class="feature-art" role="img" aria-label="Smiling woman in green top wearing headphones" style="left:160px;width:161px;background:linear-gradient(180deg,rgba(255,255,255,0),rgba(120,90,70,.25) 30%,rgba(40,160,60,.55) 75%,rgba(30,140,50,.7))"></div>
    <h2>Music by<br>Different Genre</h2>
    <p>Class aptent taciti sociosqu ad litora torquent per</p>
    <div class="more">Read More</div>
  </article>
</section>

<footer class="site-footer">
  <nav class="footer-nav">
    <a style="left:127px">HOME</a>
    <a style="left:213px">MUSIC</a>
    <a style="left:302px">ARTISTE</a>
    <a style="left:400px">NEWS</a>
    <a style="left:484px">LOGIN</a>
    <a style="left:572px">CONTACT</a>
  </nav>
  <div class="copyright">© 2017 Company Name &nbsp;All right reserved &nbsp;Term of Use</div>
  <div class="social" aria-label="Social links"><span></span><span></span><span></span><span></span></div>
</footer>
</body>
</html>
```